Business Card Design

Business Card for professional consulting firm working with large financial institutions.

Target Market(s)

Executive buyers

Industry/Entity Type

Banking

Contact Information for Business Card

Mild creativity wanted. Not boring, but do elaborate artwork.

Font styles to use
Serif
Sans Serif

Colors

Designer to choose colors to be used in the design.

Requirements
Must have
• Standard business card features - company name, individual name, telephone, website, email, locations.
Nice to have
• Two colors
Should not have
• too many colors, fancy printing, cartoons.

```html
<!DOCTYPE html>
<html lang="en">
<head>
<meta charset="utf-8">
<title>Northvale Business Card</title>
<link rel="stylesheet" href="https://fonts.googleapis.com/css2?family=Lato:wght@400;700&display=swap">
<style>
  :root {
    --backdrop: #666666;
    --card-white: #f6f6f6;
    --navy: #1a2a8c;
    --royal: #0a2c8e;
    --ink: #2b2b2b;
    --rule: #b8b8b8;
    --mark-grey: #1d2f7e;
  }
  html, body {
    margin: 0;
    padding: 0;
    width: 1200px;
    height: 802px;
    overflow: hidden;
    background: var(--backdrop);
    font-family: "Lato", Arial, sans-serif;
  }
  .stage {
    position: relative;
    width: 1200px;
    height: 802px;
  }
  .card {
    position: absolute;
    top: 274px;
    width: 443px;
    height: 265px;
    box-shadow: 0 10px 24px rgba(0,0,0,0.25);
  }
  .card-front {
    left: 136px;
    background: var(--card-white);
  }
  .card-back {
    left: 624px;
    background: var(--royal);
  }
  .brand-name {
    position: absolute;
    font-family: "Lato", Arial, sans-serif;
    font-weight: 400;
    letter-spacing: 0.5px;
    white-space: nowrap;
    transform: translate(-50%, -50%);
  }
  .card-front .brand-name {
    left: 116px;
    top: 136px;
    font-size: 26px;
    color: var(--mark-grey);
  }
  .card-back .brand-name {
    left: 346px;
    top: 117px;
    font-size: 18px;
    color: #ffffff;
  }
  .divider {
    position: absolute;
    left: 234px;
    top: 68px;
    width: 1px;
    height: 128px;
    background: var(--rule);
  }
  .contact {
    position: absolute;
    left: 253px;
    top: 68px;
    color: var(--ink);
  }
  .person-name {
    margin: 0;
    font-size: 16px;
    font-weight: 400;
    color: var(--navy);
    line-height: 19px;
    letter-spacing: 0.2px;
  }
  .person-role {
    margin: 0 0 6px;
    font-size: 12.5px;
    line-height: 15px;
  }
  .contact-list {
    list-style: none;
    margin: 0 0 8px;
    padding: 0;
    font-size: 12.5px;
    line-height: 16px;
  }
  .contact-list li {
    display: flex;
    align-items: center;
    gap: 4px;
  }
  .contact-list svg {
    width: 10px;
    height: 10px;
    fill: var(--navy);
    flex: none;
  }
  .address {
    margin: 0;
    font-style: normal;
    font-size: 12.5px;
    line-height: 15.5px;
  }
</style>
</head>
<body>
<main class="stage">
  <section class="card card-front" aria-label="Card front">
    <div class="brand-name">Northvale</div>
    <div class="divider"></div>
    <div class="contact">
      <h1 class="person-name">DANIEL HART</h1>
      <p class="person-role">Managing Director</p>
      <ul class="contact-list">
        <li>
          <svg viewBox="0 0 10 10" aria-hidden="true"><path d="M0 3.2C0 1.5 2 1 5 1s5 .5 5 2.2V4H7.3V3H2.7v1H0z M2 4.6h6L9 9H1z M5 5.3a1.3 1.3 0 1 0 0 2.6a1.3 1.3 0 1 0 0-2.6z"/></svg>
          044-987 654 321
        </li>
        <li>
          <svg viewBox="0 0 10 10" aria-hidden="true"><path d="M0 2h10v6H0z" /><path d="M0.5 2.5L5 5.8L9.5 2.5" stroke="#f6f6f6" stroke-width="1" fill="none"/></svg>
          info@northvale.com
        </li>
        <li>
          <svg viewBox="0 0 10 10" aria-hidden="true"><circle cx="5" cy="5" r="4.6"/><path d="M3 3.2c1 0 1.5.8 1 1.6s.6 1.5-.2 2.4M6.5 2c-.4 1 .6 1.6 1.6 1.3" stroke="#f6f6f6" stroke-width="0.9" fill="none"/></svg>
          www.northvale.com
        </li>
      </ul>
      <address class="address">48 Harbour Street, Suite 210<br>Eastbridge, 560217.</address>
    </div>
  </section>

  <section class="card card-back" role="img" aria-label="Card back: deep blue field with a faint repeated company name pattern">
    <div class="brand-name">Northvale</div>
  </section>
</main>
</body>
</html>
```